We are looking for a Flyer we will send through the mail for residents of Apartment Buildings

We are a laundry service doing pickup and delivery for the Manhattan Area.
We offer next day delivery on all laundry orders.
we want to send out a flyer to buildings for unbelievable promotion:

50% your first order (coupon code WASH50)
2nd order FREE! (up to $50)
FREE pickup and delivery
FREE next day service
FREE Flore and Plume
schedule now on www.rinsora.com!

We offer the cleanest and brightest laundry in the city!
Attached is our logo plus some icons to use

Target Market(s)

females ages 24-40

Industry/Entity Type

Apartment

Font styles to use
Other font styles liked:
• habraba

Requirements
Must have
• modern and clean look
• our logo
• BRIGHT COLORS
• Size of flyer will be 8.52 x 5.47
• Logo font: Harabara
• Slogan font: Swiss 721 Light Extended BT
• Dark blue: C 100 M 88 Y 0 K 0
• Light blue: C 85 M 50 Y 0 K 0
• Orange: C 0 M 80 Y 95 K 0
• Violet: C 85 M 100 Y 0 K 0
Should not have
• we dont want to be too busy

```html
<!DOCTYPE html>
<html lang="en">
<head>
<meta charset="utf-8">
<title>Rinsora Laundry Flyer</title>
<link href="https://fonts.googleapis.com/css2?family=Lato:wght@300;400;700;900&family=Great+Vibes&display=swap" rel="stylesheet">
<style>
  :root {
    --sky: #3a9fd8;
    --band: #3db8de;
    --band-deep: #2fa9d2;
    --navy: #2e3192;
    --ink: #3c3c8f;
    --orange: #f15a24;
    --grey: #6d6e71;
    --white: #ffffff;
    --border: #59bde6;
  }
  * { margin: 0; padding: 0; box-sizing: border-box; }
  html, body { width: 776px; height: 1200px; overflow: hidden; background: var(--white); }
  body { font-family: "Lato", Arial, sans-serif; }
  .flyer { position: relative; width: 776px; height: 1200px; overflow: hidden; background: var(--white); }
  .abs { position: absolute; }
  .center { left: 0; width: 776px; text-align: center; }
  .script { font-family: "Great Vibes", cursive; }

  .headline { top: 30px; font-size: 50px; font-weight: 700; color: var(--sky); letter-spacing: 0.2px; }
  .offer-lead { top: 104px; font-size: 25px; font-weight: 300; color: var(--navy); letter-spacing: 1px; }
  .offer-line { top: 148px; font-size: 29px; font-weight: 300; color: var(--navy); }
  .offer-line .script { font-size: 40px; }

  .brand { top: 270px; display: flex; justify-content: center; align-items: center; gap: 12px; }
  .brand-dot { width: 26px; height: 26px; border-radius: 50%; background: var(--sky); }
  .brand-name { font-size: 42px; font-weight: 700; color: var(--sky); }

  .service-band { left: 0; top: 403px; width: 776px; height: 393px;
    background: radial-gradient(circle at 50% 50%, var(--band), var(--band-deep)); }
  .service { position: absolute; top: 476px; width: 220px; margin-left: -110px; text-align: center; color: var(--white); }
  .service svg { display: block; margin: 0 auto; }
  .service-title { margin-top: 20px; font-size: 25px; font-weight: 700; line-height: 33px; }
  .service-note { margin-top: 10px; font-size: 16.5px; line-height: 20px; }

  .promo-lead { top: 820px; font-size: 29px; font-weight: 300; color: var(--navy); }
  .promo-lead .script { font-size: 40px; }

  .ribbon { left: 91px; top: 896px; }
  .first-order { left: 254px; top: 898px; width: 112px; text-align: center; }
  .first-order h3 { font-size: 20px; font-weight: 700; color: var(--sky); line-height: 23px; }
  .first-order p { margin-top: 6px; font-size: 15px; color: var(--grey); line-height: 18px; }
  .divider { left: 373px; top: 902px; width: 1px; height: 88px; background: #9ea3a8; }
  .second-order { left: 394px; top: 896px; width: 96px; text-align: center; color: var(--orange); }
  .second-order .label { font-size: 19px; font-weight: 700; line-height: 22px; }
  .second-order .label sup { font-size: 11px; }
  .second-order .big { font-size: 33px; font-weight: 900; line-height: 36px; }
  .second-order .cap { font-size: 14.5px; color: var(--grey); }
  .amp { left: 508px; top: 912px; font-size: 48px; color: var(--navy); }
  .freebies { left: 556px; top: 900px; color: var(--ink); font-size: 15.5px; line-height: 20px; }
  .freebies strong { color: var(--orange); font-weight: 700; }

  .schedule-box { left: 91px; top: 1043px; width: 340px; height: 97px; border: 2px solid var(--border);
    text-align: center; padding-top: 16px; }
  .schedule-box .lead { font-size: 22px; font-weight: 300; color: var(--ink); }
  .schedule-box .url { margin-top: 4px; font-size: 29px; font-weight: 700; color: var(--sky); }

  .standards { left: 450px; top: 1038px; width: 234px; text-align: center; font-size: 15.5px; line-height: 20px; color: var(--ink); }
  .partners { left: 462px; top: 1100px; display: flex; align-items: center; gap: 14px; }
  .partner-name { font-size: 17px; font-weight: 700; color: var(--navy); }
  .partner-badge { width: 34px; height: 34px; border-radius: 50%; background: #3a3a3a; }
  .partner-badge.round { background: #2e7d4f; }
</style>
</head>
<body>
<main class="flyer">
  <h1 class="abs center headline">Laundry overwhelmed?</h1>
  <p class="abs center offer-lead">WE OFFER</p>
  <p class="abs center offer-line">the <span class="script">cleanest</span> and <span class="script">brightest laundry</span> in the city!</p>

  <div class="abs center brand"><span class="brand-dot"></span><span class="brand-name">rinsora.com</span></div>

  <section class="abs service-band" role="img" aria-label="Blue band with a soft damask pattern"></section>

  <div class="service" style="left:173px">
    <svg width="100" height="112" viewBox="0 0 100 112">
      <path d="M50 4a46 46 0 1 1 0 92a46 46 0 1 1 0-92z M40 95 L50 110 L60 95z" fill="var(--white)"/>
      <circle cx="50" cy="50" r="38" fill="var(--band)"/>
      <circle cx="50" cy="52" r="15" fill="none" stroke="var(--white)" stroke-width="4"/>
      <path d="M50 44v9l6 4" stroke="var(--white)" stroke-width="3" fill="none" stroke-linecap="round"/>
      <circle cx="38" cy="36" r="5" fill="var(--white)"/><circle cx="62" cy="36" r="5" fill="var(--white)"/>
      <path d="M40 66l-4 5M60 66l4 5" stroke="var(--white)" stroke-width="3" stroke-linecap="round"/>
    </svg>
    <h2 class="service-title">Schedule<br>Pick up</h2>
    <p class="service-note">Easy Online Access<br>24 Hour Turnaround.</p>
  </div>

  <div class="service" style="left:387px">
    <svg width="100" height="112" viewBox="0 0 100 112">
      <path d="M50 4a46 46 0 1 1 0 92a46 46 0 1 1 0-92z M40 95 L50 110 L60 95z" fill="var(--white)"/>
      <circle cx="50" cy="50" r="38" fill="var(--band)"/>
      <path d="M46 30a4 4 0 1 1 4 4v3" stroke="var(--white)" stroke-width="3" fill="none" stroke-linecap="round"/>
      <path d="M28 46 L50 37 L72 46" stroke="var(--white)" stroke-width="3" fill="none" stroke-linejoin="round"/>
      <path d="M36 45 L32 54 L38 56 L38 70 L62 70 L62 56 L68 54 L64 45 L56 42 Q50 48 44 42z" fill="none" stroke="var(--white)" stroke-width="3" stroke-linejoin="round"/>
    </svg>
    <h2 class="service-title">We pick up<br>wash and fold</h2>
    <p class="service-note">5 Star Rated Laundry<br>Service</p>
  </div>

  <div class="service" style="left:596px">
    <svg width="100" height="112" viewBox="0 0 100 112">
      <path d="M50 4a46 46 0 1 1 0 92a46 46 0 1 1 0-92z M40 95 L50 110 L60 95z" fill="var(--white)"/>
      <circle cx="50" cy="50" r="38" fill="var(--band)"/>
      <rect x="26" y="38" width="30" height="22" fill="none" stroke="var(--white)" stroke-width="3"/>
      <path d="M56 44h10l7 8v8h-17z" fill="none" stroke="var(--white)" stroke-width="3" stroke-linejoin="round"/>
      <circle cx="36" cy="63" r="4" fill="var(--white)"/><circle cx="66" cy="63" r="4" fill="var(--white)"/>
    </svg>
    <h2 class="service-title">Next Day<br>Delivery</h2>
    <p class="service-note">On All Laundry<br>Orders</p>
  </div>

  <p class="abs center promo-lead">we bring to <span class="script">you</span> this <span class="script">unbelievable promotion</span>:</p>

  <svg class="abs ribbon" width="156" height="96" viewBox="0 0 156 96">
    <defs>
      <linearGradient id="ribbonFill" x1="0" y1="0" x2="1" y2="1">
        <stop offset="0" stop-color="#1b9ad6"/><stop offset="1" stop-color="#0e6fae"/>
      </linearGradient>
    </defs>
    <path d="M0 18 L150 4 L156 78 L6 92z" fill="url(#ribbonFill)"/>
    <path d="M150 4 L156 0 L156 78z" fill="#0b5a8f"/>
    <text x="10" y="72" font-family="Lato, sans-serif" font-weight="900" font-size="56" fill="#ffffff">50</text>
    <text x="82" y="50" font-family="Lato, sans-serif" font-weight="900" font-size="30" fill="#ffffff">%</text>
    <text x="84" y="70" font-family="Lato, sans-serif" font-weight="700" font-size="16" fill="#ffffff">OFF</text>
  </svg>

  <div class="abs first-order">
    <h3>Your First<br>Order</h3>
    <p>coupon code:<br>WASH50</p>
  </div>
  <div class="abs divider"></div>
  <div class="abs second-order">
    <p class="label">2<sup>nd</sup> order</p>
    <p class="big">FREE!</p>
    <p class="cap">(up to $50)</p>
  </div>
  <span class="abs amp script">&amp;</span>
  <p class="abs freebies"><strong>FREE:</strong><br>Pickup and Delivery<br>Next Day Service<br>Flore and Plume</p>

  <div class="abs schedule-box">
    <p class="lead">schedule now on</p>
    <p class="url">www.rinsora.com!</p>
  </div>

  <p class="abs standards">We use Premium Detergents and Leading Industry Standards</p>
  <div class="abs partners">
    <span class="partner-name">Plume</span>
    <span class="partner-name" style="color:var(--orange)">Flore</span>
    <span class="partner-badge"></span>
    <span class="partner-badge round"></span>
  </div>
</main>
</body>
</html>
```